Business Card Design

I already have a company logo for my company. I have a logo for the manufacturer we represent. I want a professional business card design.

```html
<!DOCTYPE html>
<html lang="en">
<head>
<meta charset="utf-8">
<title>Beacon Alert Co – Business Card</title>
<link rel="stylesheet" href="https://fonts.googleapis.com/css2?family=Montserrat:wght@400;500;700;800&display=swap">
<style>
  :root {
    --stage: #3b3b3b;
    --card: #141414;
    --card-front: #1c1c1c;
    --white: #f2f2f2;
    --grey: #bdbdbd;
    --red: #e3262d;
    --gold: #d9a516;
  }
  * { box-sizing: border-box; margin: 0; padding: 0; }
  html, body { width: 1200px; height: 688px; overflow: hidden; }
  body {
    background: var(--stage);
    font-family: "Montserrat", sans-serif;
    position: relative;
  }
  .card {
    position: absolute;
    top: 194px;
    width: 500px;
    height: 300px;
    border-radius: 4px;
    overflow: hidden;
  }
  .card--back { left: 66px; background: var(--card); }
  .card--front { left: 634px; background: var(--card-front); }

  .brand {
    display: flex;
    align-items: center;
    gap: 12px;
    font-weight: 800;
    text-transform: uppercase;
    color: var(--white);
    letter-spacing: 0.04em;
  }
  .brand__mark {
    width: 22px;
    height: 22px;
    background: var(--red);
    flex: none;
  }
  .card--back .brand {
    position: absolute;
    inset: 0;
    justify-content: center;
    font-size: 28px;
  }
  .card--front .brand {
    position: absolute;
    left: 36px;
    top: 44px;
    font-size: 30px;
  }
  .card--front .rule {
    position: absolute;
    left: 36px;
    top: 92px;
    width: 260px;
    height: 4px;
    background: var(--gold);
  }
  .contact {
    position: absolute;
    left: 36px;
    top: 132px;
    color: var(--white);
    font-size: 12px;
    line-height: 1.45;
  }
  .contact__name {
    color: var(--red);
    font-weight: 700;
    font-size: 19px;
    line-height: 1.1;
  }
  .contact__role { font-size: 12px; margin-bottom: 14px; }
  .contact__address { margin-bottom: 12px; }
  .contact__list { list-style: none; }
  .contact__list li { display: flex; align-items: center; gap: 10px; }
  .contact__list svg { width: 10px; height: 10px; fill: var(--red); flex: none; }
</style>
</head>
<body>
  <section class="card card--back" aria-label="Card back">
    <div class="brand"><span class="brand__mark"></span>Beacon Alert Co</div>
  </section>

  <section class="card card--front" aria-label="Card front">
    <div class="brand"><span class="brand__mark"></span>Beacon Alert Co</div>
    <div class="rule"></div>
    <div class="contact">
      <p class="contact__name">Dale Morgan</p>
      <p class="contact__role">Managing Director</p>
      <p class="contact__address">2840 Alder Ave<br>Ridgeview, CO 80000</p>
      <ul class="contact__list">
        <li><svg viewBox="0 0 10 10" aria-hidden="true"><path d="M2 0h2l1 3-1.5 1a6 6 0 0 0 2.5 2.5L7 5l3 1v2a2 2 0 0 1-2 2A8 8 0 0 1 0 2a2 2 0 0 1 2-2z"/></svg>555.014.2297</li>
        <li><svg viewBox="0 0 10 10" aria-hidden="true"><path d="M0 2h10v6H0z M0 2l5 3 5-3" /></svg>hello@beaconalertco.com</li>
        <li><svg viewBox="0 0 10 10" aria-hidden="true"><circle cx="5" cy="5" r="5"/></svg>www.beaconalertco.com</li>
      </ul>
    </div>
  </section>
</body>
</html>
```